Business Card Design for Occupational Medicine Start Up Company

We need to design a professional business card. We are a healthcare company providing occupational medicine services to blue collar industries. We are professional, efficient and high quality service providers.

Target Market(s)

Blue Collar Industry: Shipbuilding, Ports, Trucking Companies; The Executives and Safety Officers for these companies

Industry/Entity Type

Healthcare

Contact Information for Business Card

Logo, Name, Title, Email, Phone

Other font styles liked:
• Please match our Brand Guide

Requirements
Must have
• Our Company Colors and Logo

```html
<!DOCTYPE html>
<html lang="en">
<head>
<meta charset="utf-8">
<title>CrewCare Clinics – Business Card</title>
<link href="https://fonts.googleapis.com/css2?family=Poppins:wght@400;500;600;700&display=swap" rel="stylesheet">
<style>
  :root {
    --navy: #2c3480;
    --sky: #26a8e0;
    --amber: #f2ad4e;
    --white: #ffffff;
    --backdrop: #e6e6e6;
  }
  * { margin: 0; padding: 0; box-sizing: border-box; }
  html, body { width: 1200px; height: 1200px; overflow: hidden; }
  body {
    background: var(--backdrop);
    font-family: "Poppins", sans-serif;
    position: relative;
  }
  .card {
    position: absolute;
    left: 298px;
    width: 604px;
    height: 345px;
    overflow: hidden;
  }
  .card-front { top: 192px; background: var(--navy); }
  .card-back  { top: 662px; background: var(--white); }

  /* front */
  .front-brand {
    position: absolute;
    left: 0; right: 0; top: 102px;
    display: flex; flex-direction: column; align-items: center;
  }
  .brand-dot {
    width: 64px; height: 64px; border-radius: 50%;
    background: var(--amber);
    margin-bottom: 24px;
  }
  .brand-name {
    font-weight: 600;
    color: var(--white);
    text-align: center;
    line-height: 1.15;
  }
  .front-brand .brand-name { font-size: 24px; letter-spacing: 1px; }
  .front-brand .brand-name span { display: block; font-size: 15px; letter-spacing: 6px; }

  /* back */
  .back-brand {
    position: absolute;
    top: 40px; left: 0; right: 0;
    display: flex; align-items: center; justify-content: center; gap: 18px;
  }
  .back-brand .brand-dot { width: 64px; height: 64px; margin: 0; }
  .back-brand .brand-name { color: var(--navy); font-size: 22px; letter-spacing: 1px; }
  .back-brand .brand-name span { display: block; font-size: 14px; letter-spacing: 6px; }

  .name-tab {
    position: absolute;
    left: 19px; top: 176px;
    width: 28px; height: 40px;
    background: var(--sky);
    border-radius: 14px 14px 0 0;
  }
  .name-tab .icon { position: absolute; left: 4px; top: 7px; }
  .holder-name {
    position: absolute;
    left: 54px; top: 186px;
    font-size: 18.5px; font-weight: 700;
    color: var(--navy);
    letter-spacing: -0.2px;
  }
  .contact-band {
    position: absolute;
    left: 0; top: 213px;
    width: 100%; height: 103px;
    background: var(--sky);
    color: var(--white);
    font-size: 13px;
  }
  .contact-row {
    position: absolute;
    display: flex; align-items: center; gap: 12px;
  }
  .row-phone { left: 23px; top: 21px; }
  .row-email { left: 23px; top: 61px; }
  .row-address {
    right: 16px; top: 21px;
    text-align: right; line-height: 16px; align-items: flex-start;
  }
  .icon { width: 20px; height: 20px; display: block; flex: none; }
  .stripe { position: absolute; left: 0; width: 100%; }
  .stripe-sky { top: 323px; height: 5px; background: var(--sky); }
  .stripe-amber { top: 334px; height: 6px; background: var(--amber); }
</style>
</head>
<body>

<section class="card card-front" aria-label="Card front">
  <div class="front-brand">
    <div class="brand-dot"></div>
    <div class="brand-name">CREWCARE<span>CLINICS</span></div>
  </div>
</section>

<section class="card card-back" aria-label="Card back">
  <div class="back-brand">
    <div class="brand-dot"></div>
    <div class="brand-name">CREWCARE<span>CLINICS</span></div>
  </div>

  <div class="name-tab">
    <svg class="icon" viewBox="0 0 20 20" aria-hidden="true">
      <path d="M0 20V9a10 10 0 0 1 20 0v11z" fill="var(--amber)"/>
      <circle cx="10" cy="8" r="3" fill="none" stroke="#fff" stroke-width="1.2"/>
      <path d="M5 16a5 4 0 0 1 10 0" fill="none" stroke="#fff" stroke-width="1.2"/>
    </svg>
  </div>
  <div class="holder-name">DANIEL R. HOLLIS</div>

  <div class="contact-band">
    <div class="contact-row row-phone">
      <svg class="icon" viewBox="0 0 20 20" aria-hidden="true">
        <path d="M0 20V9a10 10 0 0 1 20 0v11z" fill="var(--amber)"/>
        <path d="M7 6.5l1.6-.4 1 2.2-1 .8a6 6 0 0 0 2.5 2.5l.8-1 2.2 1-.4 1.6c-4 .3-7.2-2.9-6.7-6.7z" fill="#fff"/>
      </svg>
      <span>+1 555-201-4480</span>
    </div>
    <div class="contact-row row-email">
      <svg class="icon" viewBox="0 0 20 20" aria-hidden="true">
        <path d="M0 20V9a10 10 0 0 1 20 0v11z" fill="var(--amber)"/>
        <rect x="5" y="9" width="10" height="7" fill="none" stroke="#fff" stroke-width="1.1"/>
        <path d="M5 9l5 4 5-4M5 16l3.5-3.5M15 16l-3.5-3.5" fill="none" stroke="#fff" stroke-width="1.1"/>
      </svg>
      <span>info@crewcareclinics.com</span>
    </div>
    <div class="contact-row row-address">
      <span>1650 Dockside Lane Port<br>City, VA 23690</span>
      <svg class="icon" viewBox="0 0 20 20" aria-hidden="true">
        <path d="M0 20V9a10 10 0 0 1 20 0v11z" fill="var(--amber)"/>
        <path d="M6 11l4-3.5 4 3.5M7 10.5V15h6v-4.5M9 15v-2.5h2V15" fill="none" stroke="#fff" stroke-width="1.1"/>
      </svg>
    </div>
  </div>

  <div class="stripe stripe-sky"></div>
  <div class="stripe stripe-amber"></div>
</section>

</body>
</html>
```